Velundra Jobs portal

Velundra Jobs is a job portal connecting job seekers and companies offering part time jobs in the Mena region, starting in the UAE. We would like to see designs that use the color blue. We have attached images to give an idea what the website should look like. When a company posts a job the job seekers are not allowed to see which company has posted a job. There should also be a coinvex gateway. On the landing page we want a catching picture that we will send.

Target Market(s)

Students and promotional workers

Logo Text

Velundra Jobs

Coding

Coded - Design and coding required

Number of Pages Required

4 page

Font styles to use
Sans Serif

Colors
33a6d7
0692cd
85cae6

```html
<!DOCTYPE html>
<html lang="en">
<head>
<meta charset="utf-8">
<title>Velundra Jobs – Job Seeker</title>
<link href="https://fonts.googleapis.com/css2?family=Open+Sans:wght@400;600&family=Roboto+Condensed:wght@400;500&display=swap" rel="stylesheet">
<style>
:root{
  --blue:#2a59a5;
  --blue-dark:#234c91;
  --teal:#3fc0c9;
  --text:#333;
  --muted:#666;
  --line:#d8d8d8;
  --panel:#f2f2f2;
  --gray:#ebebeb;
  --pink:#e8416f;
}
*{box-sizing:border-box;margin:0;padding:0}
html,body{width:1200px;height:974px;overflow:hidden}
body{position:relative;font-family:"Open Sans",sans-serif;color:var(--text);background:#fff}
.abs{position:absolute}

.header{left:0;top:0;width:1200px;height:97px;background:linear-gradient(#fdfdfd,#e9e9e9)}
.header-bar{left:0;top:97px;width:1200px;height:4px;background:var(--blue)}
.logo{left:75px;top:30px;font-family:"Open Sans",sans-serif;font-size:35px;color:var(--teal);font-weight:400;letter-spacing:.5px}
.page-title{left:310px;top:42px;font-family:"Roboto Condensed",sans-serif;font-size:27px;font-weight:500;color:#333}
.divider{top:0;width:1px;height:97px;background:var(--line)}
.badge{left:877px;top:34px;width:21px;height:17px;border-radius:9px;background:var(--pink);color:#fff;font-size:11px;text-align:center;line-height:17px}
.avatar{left:911px;top:31px;width:42px;height:42px;border-radius:50%;background:linear-gradient(#cfd6de,#6c7b8c);border:2px solid #e4e4e4}
.btn{background:var(--blue);color:#fff;font-size:12px;text-align:center;border-radius:2px;box-shadow:0 1px 2px rgba(0,0,0,.25)}
.btn-login{left:980px;top:32px;width:105px;height:36px;line-height:36px}

.sidebar{left:0;top:101px;width:269px;height:437px;box-shadow:2px 2px 5px rgba(0,0,0,.2)}
.cat{position:absolute;left:0;width:269px;display:flex;align-items:center;justify-content:center;font-size:14px;color:#333;background:linear-gradient(#fbfbfb,#f0f0f0);border-bottom:1px solid var(--line)}
.cat.active{background:var(--blue);color:#fff}
.cat svg{position:absolute;right:20px}

.filters{left:302px;top:128px;width:857px;height:70px;background:var(--panel);border:1px solid #e2e2e2}
.select{top:147px;width:218px;height:34px;background:#fff;border:1px solid #ddd;font-size:11px;color:#888;line-height:32px;padding-left:12px}
.select .arrow{position:absolute;right:0;top:0;width:26px;height:32px;border-left:1px solid #ddd}
.select .arrow::after{content:"";position:absolute;left:8px;top:13px;border-left:5px solid transparent;border-right:5px solid transparent;border-top:6px solid #333}
.btn-search{left:1034px;top:145px;width:105px;height:36px;line-height:36px}

.jobs{left:302px;top:237px;width:857px;height:301px;background:var(--panel);box-shadow:0 1px 6px rgba(0,0,0,.25)}
.jobs-head{left:0;top:0;width:857px;height:44px;background:linear-gradient(#fafafa,#ececec);font-family:"Roboto Condensed",sans-serif;font-size:16px;font-weight:500;letter-spacing:.6px;color:#333}
.jobs-head span{position:absolute;top:13px}
.row{position:absolute;left:11px;width:835px;height:43px;background:#f8f8f8;border-radius:2px;font-size:14px;color:#555}
.row.selected{background:var(--blue);color:#fff}
.row span{position:absolute;top:12px}
.check{position:absolute;left:13px;top:11px;width:20px;height:20px;border:2px solid var(--blue);border-radius:4px;background:#fff}
.row .btn{position:absolute;left:732px;top:8px;width:92px;height:27px;line-height:27px;font-size:12px;border-radius:0}

.featured{left:0;top:569px;width:1200px;height:333px;background:var(--gray)}
.featured h2{position:absolute;left:43px;top:40px;font-family:"Roboto Condensed",sans-serif;font-weight:500;font-size:27px;color:#333}
.card{position:absolute;top:92px;width:202px}
.card .photo{width:202px;height:138px}
.card h3{margin-top:10px;font-family:"Roboto Condensed",sans-serif;font-weight:500;font-size:16px;color:#333;white-space:nowrap}
.card p{margin-top:5px;font-size:11px;line-height:21px;color:#444}

.footer{left:0;top:902px;width:1200px;height:72px;background:var(--blue);color:#fff;font-size:11px}
.footer span{position:absolute;top:28px}
</style>
</head>
<body>

<header class="abs header"></header>
<div class="abs header-bar"></div>
<div class="abs logo">velundra</div>
<div class="abs page-title">Job Seeker</div>
<svg class="abs" style="left:830px;top:42px" width="22" height="22" viewBox="0 0 22 22"><circle cx="9" cy="9" r="7" fill="none" stroke="#555" stroke-width="2"/><line x1="14" y1="14" x2="20" y2="20" stroke="#555" stroke-width="2"/></svg>
<svg class="abs" style="left:870px;top:44px" width="20" height="22" viewBox="0 0 20 22"><path d="M10 2c-4 0-6 3-6 7v5l-2 3h16l-2-3V9c0-4-2-7-6-7z" fill="#666"/><circle cx="10" cy="19" r="2.5" fill="#666"/></svg>
<div class="abs badge">8</div>
<div class="abs avatar" role="img" aria-label="User profile photo"></div>
<div class="abs divider" style="left:962px"></div>
<div class="abs divider" style="left:1100px"></div>
<div class="abs btn btn-login">LOGIN</div>

<nav class="abs sidebar">
  <div class="cat active" style="top:0;height:53px">Finibus Bonor (286)<svg width="10" height="14" viewBox="0 0 10 14"><path d="M2 1l6 6-6 6" fill="none" stroke="#fff" stroke-width="2"/></svg></div>
  <div class="cat" style="top:53px;height:47px">Voluptatem ac (156)<svg width="10" height="14" viewBox="0 0 10 14"><path d="M2 1l6 6-6 6" fill="none" stroke="#888" stroke-width="1.5"/></svg></div>
  <div class="cat" style="top:100px;height:43px">Doloremque la (12)<svg width="10" height="14" viewBox="0 0 10 14"><path d="M2 1l6 6-6 6" fill="none" stroke="#888" stroke-width="1.5"/></svg></div>
  <div class="cat" style="top:143px;height:43px">Totam rem&nbsp; (23)<svg width="10" height="14" viewBox="0 0 10 14"><path d="M2 1l6 6-6 6" fill="none" stroke="#888" stroke-width="1.5"/></svg></div>
  <div class="cat" style="top:186px;height:43px">Accusantium do (78)<svg width="10" height="14" viewBox="0 0 10 14"><path d="M2 1l6 6-6 6" fill="none" stroke="#888" stroke-width="1.5"/></svg></div>
  <div class="cat" style="top:229px;height:42px">Rem aperiam (52)<svg width="10" height="14" viewBox="0 0 10 14"><path d="M2 1l6 6-6 6" fill="none" stroke="#888" stroke-width="1.5"/></svg></div>
  <div class="cat" style="top:271px;height:43px">Nemo enim&nbsp; (55)<svg width="10" height="14" viewBox="0 0 10 14"><path d="M2 1l6 6-6 6" fill="none" stroke="#888" stroke-width="1.5"/></svg></div>
  <div class="cat" style="top:314px;height:40px">Quia voluptas&nbsp; (77)<svg width="10" height="14" viewBox="0 0 10 14"><path d="M2 1l6 6-6 6" fill="none" stroke="#888" stroke-width="1.5"/></svg></div>
  <div class="cat" style="top:354px;height:42px">Qui dolorem&nbsp;&nbsp; (45)<svg width="10" height="14" viewBox="0 0 10 14"><path d="M2 1l6 6-6 6" fill="none" stroke="#888" stroke-width="1.5"/></svg></div>
  <div class="cat" style="top:396px;height:41px">Dolor sit amet (52)<svg width="10" height="14" viewBox="0 0 10 14"><path d="M2 1l6 6-6 6" fill="none" stroke="#888" stroke-width="1.5"/></svg></div>
</nav>

<section class="abs filters"></section>
<div class="abs select" style="left:319px">Work offered<span class="arrow"></span></div>
<div class="abs select" style="left:557px">Location<span class="arrow"></span></div>
<div class="abs select" style="left:793px">Languages<span class="arrow"></span></div>
<div class="abs btn btn-search">LOGIN</div>

<section class="abs jobs">
  <div class="abs jobs-head">
    <span style="left:16px">Job title</span>
    <span style="left:345px">Due Date</span>
    <span style="left:535px;top:19px">Provider name</span>
  </div>
  <div class="row selected" style="top:64px">
    <div class="check"><svg width="16" height="16" viewBox="0 0 16 16"><path d="M3 8l3 3 7-7" fill="none" stroke="#2a59a5" stroke-width="2.2"/></svg></div>
    <span style="left:46px">Finibus Bonorum et Malorum</span><span style="left:335px">23 Jan 2015</span><span style="left:529px">Provider1</span>
    <div class="btn">Apply now</div>
  </div>
  <div class="row" style="top:117px">
    <div class="check"></div>
    <span style="left:42px">Sed quia consequuntur</span><span style="left:335px">23 Jan 2015</span><span style="left:529px">Provider1</span>
    <div class="btn">Apply now</div>
  </div>
  <div class="row" style="top:172px">
    <div class="check"></div>
    <span style="left:43px">Magni dolores eos qui</span><span style="left:335px">23 Jan 2015</span><span style="left:529px">Provider1</span>
    <div class="btn">Apply now</div>
  </div>
  <div class="row" style="top:226px">
    <div class="check"></div>
    <span style="left:43px">Vitae dicta sunt explicabo</span><span style="left:335px">23 Jan 2015</span><span style="left:529px">Provider1</span>
    <div class="btn">Apply now</div>
  </div>
</section>

<section class="abs featured">
  <h2>Featured Job Provider</h2>
  <div class="card" style="left:43px"><div class="photo" role="img" aria-label="Business handshake in an office" style="background:linear-gradient(135deg,#c9dced,#3a4f70)"></div><h3>Accusantium doloremque</h3><p>Lorem Ipsum is simply dummy text of the printing and typesetting</p></div>
  <div class="card" style="left:272px"><div class="photo" role="img" aria-label="Hand presenting small business figures" style="background:linear-gradient(135deg,#2b3440,#8fa3b8)"></div><h3>Eaque ipsa quae ab</h3><p>Lorem Ipsum is simply dummy text of the printing and typesetting</p></div>
  <div class="card" style="left:501px"><div class="photo" role="img" aria-label="Team meeting around a laptop" style="background:linear-gradient(135deg,#d8d8d6,#5a5b5e)"></div><h3>Veritatis et quasi architecto</h3><p>Lorem Ipsum is simply dummy text of the printing and typesetting</p></div>
  <div class="card" style="left:728px"><div class="photo" role="img" aria-label="Two businessmen reviewing a tablet" style="background:linear-gradient(135deg,#9fc2e0,#2a3446)"></div><h3>Featured Job Provider</h3><p>Lorem Ipsum is simply dummy text of the printing and typesetting</p></div>
  <div class="card" style="left:955px"><div class="photo" role="img" aria-label="Colleagues working together at a desk" style="background:linear-gradient(135deg,#efe6da,#4a4a50)"></div><h3>Voluptatem quia voluptas</h3><p>Lorem Ipsum is simply dummy text of the printing and typesetting</p></div>
</section>

<footer class="abs footer">
  <span style="left:98px">Copyrights © Velundra 2015 . All Rights Reserved</span>
  <span style="left:829px">About us</span>
  <span style="left:910px">Terms and conditions</span>
  <span style="left:1058px">Sitemap</span>
  <span style="left:1145px">C12</span>
</footer>

</body>
</html>
```